Business Card for Field Lotus-Eco Friendly Organic Clothing Brand

We are looking for an amazing business card for our eco friendly, organic clothing brand. We are thinking maybe a business card with a peel off sticker on the back, since our hanging clothing tag is a peel off sticker on the back. I will attach our hang tag so we can make sure we stay in line with our design. I've also attached a bag we are doing because I do like the scattered emblem look as well.

```html
<!DOCTYPE html>
<html lang="en">
<head>
<meta charset="utf-8">
<title>Field Lotus – Business Card</title>
<link rel="stylesheet" href="https://fonts.googleapis.com/css2?family=Arimo:ital,wght@0,400;0,700;1,700&display=swap">
<style>
  :root {
    --page: #e9e6df;
    --card-black: #141414;
    --card-black-soft: #1e1e1c;
    --gold: #d8a928;
    --gold-light: #f3d36a;
    --gold-dark: #8a6a14;
    --panel: #ffffff;
    --ink: #1a1a1a;
    --ink-soft: #555555;
    --camo-a: #e2c45a;
    --camo-b: #6f6a2a;
  }
  * { box-sizing: border-box; margin: 0; padding: 0; }
  html, body { width: 1200px; height: 950px; overflow: hidden; }
  body {
    background: var(--page);
    font-family: "Arimo", Arial, sans-serif;
    position: relative;
  }
  .card {
    position: absolute;
    width: 680px;
    height: 390px;
    border-radius: 18px;
    overflow: hidden;
    box-shadow: 0 10px 28px rgba(0,0,0,0.28);
  }
  .card svg.card-art { position: absolute; inset: 0; }

  /* Back card */
  .card-back { left: 260px; top: 40px; background: var(--card-black-soft); }
  .back-pattern {
    position: absolute; inset: 0;
    background: radial-gradient(ellipse at 50% 45%, #2a2a27 0%, var(--card-black) 75%);
  }
  .lockup {
    position: absolute; left: 170px; top: 120px;
    display: flex; align-items: center; gap: 0;
    transform: rotate(-4deg);
  }
  .lockup-mark {
    width: 120px; height: 120px;
    border: 3px solid var(--gold);
    background: #0c0c0c;
    display: flex; align-items: center; justify-content: center;
    position: relative; z-index: 2;
    transform: rotate(-6deg);
  }
  .figure-fill {
    border-radius: 50% 50% 18% 18%;
    background: linear-gradient(160deg, var(--camo-a), var(--camo-b));
  }
  .lockup-mark .figure-fill { width: 82px; height: 88px; }
  .lockup-label {
    margin-left: -10px;
    width: 220px; height: 108px;
    border: 3px solid var(--gold);
    border-radius: 6px;
    background: #0c0c0c;
    display: flex; flex-direction: column; align-items: center; justify-content: center;
    gap: 10px;
  }
  .brand-name {
    font-weight: 700; font-size: 30px; color: var(--gold-light);
    letter-spacing: 0.5px;
  }
  .brand-web { font-size: 11px; color: var(--gold); }

  /* Front card */
  .card-front { left: 260px; top: 500px; background: var(--card-black); }
  .emblem {
    position: absolute; left: 58px; top: 42px;
    width: 230px; height: 230px;
    transform: rotate(-10deg);
    background: #0a0a0a;
    border: 4px solid var(--gold);
    box-shadow: 0 0 0 2px #0a0a0a, 0 0 0 4px var(--gold-dark);
    display: flex; align-items: center; justify-content: center;
  }
  .emblem .figure-fill { width: 150px; height: 165px; }
  .contact {
    position: absolute; left: 345px; top: 128px;
    color: var(--ink);
  }
  .person-name { font-weight: 700; font-size: 24px; }
  .person-role { font-weight: 700; font-style: italic; font-size: 15px; margin-top: 2px; }
  .address { margin-top: 14px; font-size: 16px; line-height: 20px; color: var(--ink-soft); }
  .lines { list-style: none; margin-top: 2px; font-size: 16px; line-height: 22px; color: var(--ink-soft); }
  .lines li { display: flex; align-items: center; gap: 7px; }
  .lines svg { width: 13px; height: 13px; fill: var(--gold); flex: none; }
</style>
</head>
<body>

<section class="card card-back" aria-label="Card back">
  <div class="back-pattern" role="img" aria-label="Dark background with faint scattered words and peace and heart emblems"></div>
  <div class="lockup">
    <div class="lockup-mark">
      <div class="figure-fill" role="img" aria-label="Camouflage meditating figure emblem"></div>
    </div>
    <div class="lockup-label">
      <span class="brand-name">Field Lotus</span>
      <span class="brand-web">www.fieldlotus.com</span>
    </div>
  </div>
</section>

<section class="card card-front" aria-label="Card front">
  <svg class="card-art" width="680" height="390" viewBox="0 0 680 390">
    <rect x="10" y="10" width="660" height="370" rx="14" fill="none" stroke="var(--gold)" stroke-width="2"/>
    <path d="M40 24 H642 Q656 24 656 38 V352 Q656 366 642 366 H38 Q24 366 24 352 V210 Z" fill="var(--panel)"/>
    <path d="M40 24 H642 Q656 24 656 38 V352 Q656 366 642 366 H38 Q24 366 24 352 V210" fill="none" stroke="var(--gold)" stroke-width="1.5"/>
  </svg>

  <div class="emblem">
    <div class="figure-fill" role="img" aria-label="Camouflage meditating figure emblem"></div>
  </div>

  <div class="contact">
    <p class="person-name">Mara Kellen</p>
    <p class="person-role">President</p>
    <p class="address">2170 Orchard Lane<br>Cedar Vale, NY 10980</p>
    <ul class="lines">
      <li><svg viewBox="0 0 16 16"><path d="M3 1l3 3-2 2c1 2 3 4 5 5l2-2 3 3-2 3C6 14 2 10 1 3z"/></svg>555 0142 3381</li>
      <li><svg viewBox="0 0 16 16"><path d="M4 0h8v16H4zM6 2v10h4V2z"/></svg>555 0176 2094</li>
      <li><svg viewBox="0 0 16 16"><path d="M4 1h8v4H4zM1 6h14v7h-3v3H4v-3H1zM6 11v3h4v-3z"/></svg>555 0193 4427</li>
      <li><svg viewBox="0 0 16 16"><path d="M1 3h14v10H1zM2 4l6 5 6-5z"/></svg>info@fieldlotus.com</li>
    </ul>
  </div>
</section>

</body>
</html>
```